real esate business card with company logo and name

we need a business card design for a real esate company

The company name is Walsh & Brand Pty Ltd, and we have our logo designed and will upload. We want classic or moden feel. Black or white background. looks more textured. Should include folowinginformations
Owen Walsh and Lucy Brand
Sales Agents & Onsite Manager
p: 07 5948 2063
F: 07 5948 2174
M:0431 857 219
3/42 Marlow Crescent, FERNLEA QLD 4213

We want this business card looks professonal. Thank you in advance.

Industry/Entity Type

Real Estate Agent

Contact Information for Business Card

Owen Walsh and Lucy Brand
Onsite Manager & Sales Agents
p: 07 5948 2063
M:0431 857 219

Font styles to use
Serif

Colors
000000
fbfbfb
333333
959595

Requirements
Must have
• company logo and name, black or white back ground

```html
<!DOCTYPE html>
<html lang="en">
<head>
<meta charset="utf-8">
<title>Walsh &amp; Brand Pty Ltd — Business Card</title>
<link rel="stylesheet" href="https://fonts.googleapis.com/css2?family=Tinos:wght@400;700&display=swap">
<style>
  :root {
    --ink: #000000;
    --paper: #fbfbfb;
    --charcoal: #333333;
    --silver: #959595;
    --backdrop: #e4e2df;
  }
  * { box-sizing: border-box; margin: 0; padding: 0; }
  html, body {
    width: 1200px;
    height: 892px;
    overflow: hidden;
    background: var(--backdrop);
  }
  .card {
    position: absolute;
    left: 100px;
    top: 160px;
    width: 1000px;
    height: 572px;
    background: linear-gradient(135deg, #ffffff 0%, var(--paper) 55%, #ececec 100%);
    box-shadow: 0 10px 30px rgba(0,0,0,0.18);
    overflow: hidden;
    font-family: "Tinos", "Times New Roman", serif;
    color: var(--ink);
  }
  .card-swoosh {
    position: absolute;
    left: 0;
    top: 0;
    width: 1000px;
    height: 572px;
  }
  .brand {
    position: absolute;
    left: 200px;
    top: 220px;
    width: 280px;
    text-align: center;
  }
  .brand-mark {
    display: block;
    width: 54px;
    height: 54px;
    margin: 0 auto 22px;
    background: var(--silver);
  }
  .brand-name {
    font-size: 19px;
    font-weight: 400;
    letter-spacing: 1px;
    text-transform: uppercase;
    color: var(--silver);
    white-space: nowrap;
  }
  .divider {
    position: absolute;
    left: 520px;
    top: 120px;
    width: 3px;
    height: 330px;
    background: var(--ink);
  }
  .details {
    position: absolute;
    left: 575px;
    top: 112px;
  }
  .person-name {
    font-size: 40px;
    font-weight: 400;
    line-height: 1.05;
    color: var(--ink);
  }
  .person-role {
    font-size: 22px;
    color: var(--charcoal);
    margin-bottom: 16px;
  }
  .contact-list {
    list-style: none;
    margin-top: 14px;
    font-size: 24px;
    line-height: 1.3;
  }
  .contact-list li {
    display: flex;
    align-items: flex-start;
    gap: 12px;
  }
  .contact-icon {
    flex: none;
    width: 19px;
    height: 19px;
    margin-top: 5px;
  }
</style>
</head>
<body>
  <article class="card">
    <svg class="card-swoosh" viewBox="0 0 1000 572" aria-hidden="true">
      <defs>
        <linearGradient id="gloss-black" x1="0" y1="0" x2="1" y2="1">
          <stop offset="0" stop-color="#2a2a2a"/>
          <stop offset="0.5" stop-color="#000"/>
          <stop offset="1" stop-color="#1a1a1a"/>
        </linearGradient>
        <linearGradient id="gloss-grey" x1="0" y1="0" x2="0" y2="1">
          <stop offset="0" stop-color="#5a5a5a"/>
          <stop offset="1" stop-color="#333"/>
        </linearGradient>
      </defs>
      <path d="M0,0 H70 C140,180 140,400 60,572 H0 Z" fill="url(#gloss-grey)"/>
      <path d="M92,0 H250 C165,90 125,195 116,300 C110,190 104,90 92,0 Z" fill="url(#gloss-black)"/>
      <path d="M150,572 C175,470 240,410 340,390 C260,440 230,500 225,572 Z" fill="url(#gloss-black)"/>
      <path d="M360,572 C390,540 440,520 500,515 C450,535 425,552 415,572 Z" fill="#111"/>
    </svg>

    <div class="brand">
      <span class="brand-mark"></span>
      <p class="brand-name">Walsh &amp; Brand Pty Ltd.</p>
    </div>

    <div class="divider"></div>

    <section class="details">
      <h1 class="person-name">Owen Walsh</h1>
      <p class="person-role">Onsite Manager</p>
      <h2 class="person-name">Lucy Brand</h2>
      <p class="person-role">Sales Agents</p>

      <ul class="contact-list">
        <li>
          <svg class="contact-icon" viewBox="0 0 20 20" aria-label="Phone">
            <rect width="20" height="20" rx="2" fill="#000"/>
            <path d="M6 4 L8.5 4 L9.5 7 L8 8.2 C8.8 10 10 11.2 11.8 12 L13 10.5 L16 11.5 L16 14 C16 15 15 16 14 16 C8.5 15.6 4.4 11.5 4 6 C4 5 5 4 6 4 Z" fill="#fff"/>
          </svg>
          <span>07 5948 2063</span>
        </li>
        <li>
          <svg class="contact-icon" viewBox="0 0 20 20" aria-label="Mobile">
            <rect width="20" height="20" rx="2" fill="#000"/>
            <rect x="6" y="3" width="8" height="14" rx="1.2" fill="#fff"/>
            <rect x="7.3" y="5" width="5.4" height="8" fill="#000"/>
            <circle cx="10" cy="15" r="0.9" fill="#000"/>
          </svg>
          <span>0431 857 219</span>
        </li>
        <li>
          <svg class="contact-icon" viewBox="0 0 20 20" aria-label="Address">
            <rect width="20" height="20" rx="2" fill="#000"/>
            <path d="M10 3 C7 3 5 5.2 5 8 C5 11.5 10 17 10 17 C10 17 15 11.5 15 8 C15 5.2 13 3 10 3 Z" fill="#fff"/>
            <circle cx="10" cy="8" r="2" fill="#000"/>
          </svg>
          <span>3/42 Marlow Crescent, FERNLEA<br>QLD 4213</span>
        </li>
      </ul>
    </section>
  </article>
</body>
</html>
```